Hollow Meridian Book website design.

This is a simple one-page web design for my book.
I have all files and video needed.
Domain listed with Net Harbor.
Password and username will be given to winning bid.
Domain address, www.hollowmeridian.info
Upload a 30 second video so it can be played on the website.
Book cover photo
Book Blurb text.
Links to Rivermart and Audio books where the book can be purchased.
Below is the link to the Rivermart listing.
https://www.rivermart.example/dp/X00AAAAAA1/?coliid=QWERTYUIOPASD&colid=1ZXCVBNMLKJH0&psc=0&ref_=lv_ov_lig_dp_i
Below is the link to my Listenly books.com listing.
https://www.listenly.example/pd/Hollow-Meridian-Audiobook/X00BBBBBB2?qid=1000000001&sr=1-7&ref=a_search_c3_lProduct_1_7&pf_rd_p=00000000-aaaa-bbbb-cccc-000000000000&pf_rd_r=ZZZZ00000000000000QQ
Text on page.” Click on either logo to go directly to Rivermart or Listenly.com
Link Listenly book logo to my book on Listenly.com
Place this text under Listenly.com logo: “Free to new members of Listenly.com”
Link Rivermart logo to my book on Rivermart.
Place this text under Rivermart logo “ Free to new Pagewisp members on Rivermart.com”
Link the book photo to the Rivermart.com web address as well.
Enter meta tags or keywords below for search engines to locate webpage.
Hollow Meridian
Conspiracy
Conspiracy Books
Spy books
Thriller books
Suspense books
Comedy books
Dorian Welbeck

```html
<!DOCTYPE html>
<html lang="en">
<head>
<meta charset="utf-8">
<title>Hollow Meridian — Dorian Welbeck</title>
<meta name="keywords" content="Hollow Meridian, Conspiracy, Conspiracy Books, Spy books, Thriller books, Suspense books, Comedy books, Dorian Welbeck">
<link rel="stylesheet" href="https://fonts.googleapis.com/css2?family=Playfair+Display:wght@500;600&family=Open+Sans:wght@400;600&display=swap">
<style>
  :root {
    --royal: #1749c4;
    --heading: #1a3e9e;
    --navy: #1d2f6b;
    --ink: #1c1c1c;
    --link: #2a5db0;
    --pill-line: #a9a9a9;
    --rule: #f0f0f0;
    --footer: #000000;
    --paper: #ffffff;
  }
  * { box-sizing: border-box; margin: 0; padding: 0; }
  html, body { width: 730px; height: 1200px; overflow: hidden; background: var(--paper); }
  body { position: relative; font-family: "Open Sans", sans-serif; color: var(--ink); }

  .hero {
    position: absolute; left: 0; top: 0; width: 730px; height: 375px;
    background:
      radial-gradient(ellipse at 50% 45%, rgba(120,90,70,.55), transparent 60%),
      linear-gradient(180deg, #2b3033 0%, #3a3330 45%, #1d1815 100%);
  }
  .hero-title {
    position: absolute; left: 0; right: 0; top: 153px; text-align: center;
    font-family: "Playfair Display", serif; font-weight: 600; color: #fff;
    font-size: 27px; letter-spacing: .3px;
  }
  .hero-author {
    position: absolute; left: 0; right: 0; top: 193px; text-align: center;
    font-family: "Playfair Display", serif; font-weight: 600; color: #fff;
    font-size: 20px;
  }

  .rule-v { position: absolute; left: 346px; top: 411px; width: 1px; height: 353px; background: var(--rule); }
  .rule-h { position: absolute; left: 0; top: 764px; width: 347px; height: 1px; background: var(--rule); }

  .block { position: absolute; }
  .block.blue { background: var(--royal); }
  .block.frame { border: 1px solid var(--navy); }
  .cover {
    position: absolute; border-radius: 3px;
    box-shadow: 6px 10px 18px rgba(0,0,0,.25);
  }
  .cover.print {
    left: 90px; top: 455px; width: 189px; height: 275px;
    background: linear-gradient(160deg, #1d2a6a 0%, #0d0d0d 35%, #7a1515 60%, #0b0b0b 100%);
    transform: skewY(-4deg);
  }
  .cover.audio {
    left: 459px; top: 810px; width: 188px; height: 266px;
    background: linear-gradient(180deg, #050505 0%, #111 40%, #3a3a3a 65%, #0a0a0a 100%);
    transform: skewY(5deg);
  }

  .section-title {
    font-family: "Playfair Display", serif; font-weight: 600;
    color: var(--heading); font-size: 20px; letter-spacing: .2px;
  }
  .blurb {
    font-size: 10.3px; line-height: 18.3px; text-align: justify;
    text-align-last: left; margin-top: 12px;
  }
  .store-pill {
    display: flex; align-items: stretch; width: 265px; height: 60px;
    border: 1px solid var(--pill-line); border-radius: 30px; margin-top: 19px;
    text-decoration: none; color: var(--ink);
  }
  .store-name {
    width: 103px; border-right: 1px solid var(--pill-line);
    display: flex; align-items: center; justify-content: center;
    font-weight: 600; font-size: 15px; color: var(--ink);
  }
  .store-note {
    flex: 1; display: flex; align-items: center; padding-left: 15px;
    font-size: 10.3px; line-height: 18.3px;
  }
  .store-link {
    display: inline-block; margin-top: 12px; font-size: 10.3px;
    color: var(--link); text-decoration: underline;
  }
  .copy.print { position: absolute; left: 347px; top: 441px; width: 314px; }
  .copy.audio { position: absolute; left: 67px; top: 806px; width: 314px; }

  .footer {
    position: absolute; left: 0; top: 1154px; width: 730px; height: 46px;
    background: var(--footer); color: #fff;
    display: flex; align-items: center; justify-content: center; font-size: 10.3px;
  }
  .footer-code { position: absolute; right: 28px; font-size: 7px; }
</style>
</head>
<body>
  <header class="hero" role="img" aria-label="Video still: blurred crowd of commuters on a busy city street at night">
    <h1 class="hero-title">HOLLOW MERIDIAN</h1>
    <p class="hero-author">DORIAN WELBECK</p>
  </header>

  <div class="rule-v"></div>
  <div class="rule-h"></div>

  <div class="block blue" style="left:68px;top:432px;width:185px;height:252px"></div>
  <div class="block frame" style="left:78px;top:421px;width:186px;height:254px"></div>
  <div class="block blue" style="left:209px;top:634px;width:77px;height:78px"></div>
  <a href="https://www.rivermart.example/dp/X00AAAAAA1/?coliid=QWERTYUIOPASD&colid=1ZXCVBNMLKJH0&psc=0&ref_=lv_ov_lig_dp_i">
    <div class="cover print" role="img" aria-label="Hardcover book of Hollow Meridian by Dorian Welbeck with flag and portrait artwork"></div>
  </a>

  <section class="copy print">
    <h2 class="section-title">HOLLOW MERIDIAN</h2>
    <p class="blurb">A fictional novel based on current events surrounding the covid 19 virous. Jack Holman is a well-respected independent journalist contracted by the Harbor City Ledger, upon his return from reporting on the war in Syria he is tasked to investigate the covid virus outbreak in China. As he digs deeper, he uncovers a hideous plot by the powers that be here in America. Jack risks life and limb to uncover the conspirers behind all of this and shed light to the American people.</p>
    <a class="store-pill" href="https://www.rivermart.example/dp/X00AAAAAA1/?coliid=QWERTYUIOPASD&colid=1ZXCVBNMLKJH0&psc=0&ref_=lv_ov_lig_dp_i">
      <span class="store-name">Rivermart</span>
      <span class="store-note">Free to new Pagewisp<br>members on Rivermart.com</span>
    </a>
    <a class="store-link" href="https://www.rivermart.example/dp/X00AAAAAA1/?coliid=QWERTYUIOPASD&colid=1ZXCVBNMLKJH0&psc=0&ref_=lv_ov_lig_dp_i">Click to go directly to Rivermart.com</a>
  </section>

  <section class="copy audio">
    <h2 class="section-title">LISTENLY</h2>
    <p class="blurb">A fictional novel based on current events surrounding the covid 19 virous. Jack Holman is a well-respected independent journalist contracted by the Harbor City Ledger, upon his return from reporting on the war in Syria he is tasked to investigate the covid virus outbreak in China. As he digs deeper, he uncovers a hideous plot by the powers that be here in America. Jack risks life and limb to uncover the conspirers behind all of this and shed light to the American people.</p>
    <a class="store-pill" href="https://www.listenly.example/pd/Hollow-Meridian-Audiobook/X00BBBBBB2?qid=1000000001&sr=1-7&ref=a_search_c3_lProduct_1_7&pf_rd_p=00000000-aaaa-bbbb-cccc-000000000000&pf_rd_r=ZZZZ00000000000000QQ">
      <span class="store-name">Listenly</span>
      <span class="store-note">Free to new Pagewisp<br>members on Listenly.com</span>
    </a>
    <a class="store-link" href="https://www.listenly.example/pd/Hollow-Meridian-Audiobook/X00BBBBBB2?qid=1000000001&sr=1-7&ref=a_search_c3_lProduct_1_7&pf_rd_p=00000000-aaaa-bbbb-cccc-000000000000&pf_rd_r=ZZZZ00000000000000QQ">Click to go directly to Listenly.com</a>
  </section>

  <div class="block blue" style="left:475px;top:797px;width:186px;height:253px"></div>
  <div class="block frame" style="left:455px;top:807px;width:186px;height:254px"></div>
  <div class="block blue" style="left:435px;top:1004px;width:77px;height:78px"></div>
  <div class="cover audio" role="img" aria-label="Audiobook cover of Hollow Meridian by Dorian Welbeck with black title band and portrait artwork"></div>

  <footer class="footer">
    <span>2022 Hollow Meridian. All Rights Reserved.</span>
    <span class="footer-code">C50</span>
  </footer>
</body>
</html>
```